Business Card Design

We are a law firm which provides services to creditors.....we do collection litigation. I am wide open on suggestions. I was thinking of a square card? Alternatively, a vertically oriented standard card or a folded card.....something unique. I would like to use my firm logo and beyond that, I am open for any and all suggestions. I'm uncertain if the complete log is uploaded? If not, please let me email it to you.

Industry/Entity Type

Law Firm

Contact Information for Business Card

Hart, Crane & Dobbs, P.C.
Tom Dobbs, Lawyer
4387 N Larkspur Ave
Oklahoma City, OK 73924
tdobbs@HcdCounsel.com
www.HcdCounsel.com
mobile: 405-382-7914

```html
<!DOCTYPE html>
<html lang="en">
<head>
<meta charset="utf-8">
<title>Hart, Crane &amp; Dobbs, P.C. – Business Card</title>
<link rel="stylesheet" href="https://fonts.googleapis.com/css2?family=Arimo:wght@400&display=swap">
<style>
  :root {
    --backdrop: #e9e6e1;
    --card: #ffffff;
    --card-edge: #dcdad6;
    --accent: #c9652c;
    --accent-soft: #b8764e;
    --mark: #c9652c;
  }
  * { margin: 0; padding: 0; box-sizing: border-box; }
  html, body {
    width: 1200px; height: 892px; overflow: hidden;
    background: var(--backdrop);
    font-family: "Arimo", Arial, sans-serif;
  }
  .stage {
    width: 1200px; height: 892px;
    display: flex; align-items: center; justify-content: center; gap: 90px;
  }
  .card {
    width: 340px; height: 595px;
    background: var(--card);
    border: 1px solid var(--card-edge);
    box-shadow: 0 6px 18px rgba(0,0,0,0.12);
    display: flex; flex-direction: column; align-items: center;
    color: var(--accent);
    text-align: center;
  }
  .firm-mark {
    margin-top: 70px;
    display: flex; align-items: center; gap: 12px;
    font-size: 19px; color: var(--mark);
  }
  .firm-mark .dot {
    width: 26px; height: 26px; border-radius: 50%;
    background: var(--mark); flex: none;
  }
  .card-front .person-name {
    margin-top: 110px;
    font-size: 44px; font-weight: 400; letter-spacing: -0.5px;
  }
  .card-front .person-title {
    margin-top: 2px;
    font-size: 15px; color: var(--accent-soft);
  }
  .contact {
    margin-top: 70px;
    list-style: none;
    font-size: 17px; line-height: 1.45;
  }
  .card-back .firm-name {
    margin-top: 150px;
    font-size: 40px; font-weight: 400; line-height: 1.1; letter-spacing: -0.3px;
  }
</style>
</head>
<body>
<main class="stage">
  <section class="card card-front" aria-label="Card front">
    <div class="firm-mark"><span class="dot"></span><span>Hart, Crane &amp; Dobbs</span></div>
    <h1 class="person-name">Tom Dobbs</h1>
    <p class="person-title">Lawyer</p>
    <ul class="contact">
      <li>405-382-7914</li>
      <li>www.HcdCounsel.com</li>
      <li>tdobbs@HcdCounsel.com</li>
      <li>4387 N Larkspur Ave Oklahoma City,</li>
      <li>OK 73924</li>
    </ul>
  </section>

  <section class="card card-back" aria-label="Card back">
    <div class="firm-mark"><span class="dot"></span><span>Hart, Crane &amp; Dobbs</span></div>
    <h2 class="firm-name">Hart, Crane &amp; Dobbs<br>P.C.</h2>
  </section>
</main>
</body>
</html>
```